KDWB Business Card

Looking for a business card design to incorporate our branding. We want to only use the colors listing in the Branding Package (attached).
Updates

Target Market(s)

People who need their phone or device fixed.

Industry/Entity Type

Electronics

Contact Information for Business Card

Please use:

Brightwick Gadget Clinic LLC
4810 E Harlow Ridge Rd
Suite 417
San Antonio, TX 78163

Marcus Delgrove, Store Manager

(210) 555-0147

Requirements
Must have
• Must include the colors that are contained within the Branding Package PDF file.

```html
<!DOCTYPE html>
<html lang="en">
<head>
<meta charset="utf-8">
<title>Brightwick Gadget Clinic – Business Card</title>
<link rel="stylesheet" href="https://fonts.googleapis.com/css2?family=Lato:wght@300;400&display=swap">
<style>
  :root {
    --bg: #e9e7e3;
    --card: #ffffff;
    --orange: #e8562a;
    --charcoal: #4d4e50;
    --ink: #4a4a4a;
    --rule: #8a8a8a;
    --shadow: rgba(0, 0, 0, 0.16);
  }
  * { box-sizing: border-box; margin: 0; padding: 0; }
  html, body {
    width: 1200px; height: 892px; overflow: hidden;
    background: var(--bg);
    font-family: "Lato", sans-serif;
    color: var(--ink);
  }
  .sheet {
    width: 1200px; height: 892px;
    display: flex; align-items: center; justify-content: center; gap: 60px;
  }
  .card {
    position: relative;
    width: 525px; height: 300px;
    background: var(--card);
    box-shadow: 0 6px 18px var(--shadow);
    overflow: hidden;
  }

  /* brand lockup */
  .brand { display: flex; align-items: center; gap: 14px; }
  .brand-mark { width: 40px; height: 40px; background: var(--orange); border-radius: 6px; flex: none; }
  .brand-name { font-weight: 300; font-size: 28px; color: var(--orange); line-height: 1; letter-spacing: 0.3px; }

  /* front */
  .card-front .brand { position: absolute; left: 44px; top: 44px; }
  .band-rule { position: absolute; left: 0; width: 100%; height: 3px; background: var(--orange); }
  .band-rule.top { top: 120px; }
  .band-rule.bottom { top: 184px; }
  .name-band {
    position: absolute; left: 0; top: 127px; width: 100%; height: 53px;
    background: var(--charcoal);
    display: flex; align-items: center; padding-left: 44px; gap: 16px;
    color: #fff;
  }
  .person-name { font-weight: 300; font-size: 26px; letter-spacing: 0.3px; }
  .band-divider { width: 2px; height: 24px; background: #fff; }
  .person-role { font-weight: 300; font-size: 13px; color: #e4e4e4; }

  .contact-row {
    position: absolute; left: 44px; right: 30px; top: 212px;
    display: flex; align-items: center; gap: 22px;
  }
  .phone { display: flex; align-items: center; gap: 9px; font-size: 15px; font-weight: 400; }
  .phone-icon { width: 14px; height: 14px; background: var(--orange); display: flex; align-items: center; justify-content: center; }
  .contact-divider { width: 1px; height: 54px; background: var(--rule); }
  .address { font-size: 15px; font-weight: 400; line-height: 1.3; }

  /* back */
  .card-back { display: flex; flex-direction: column; align-items: center; justify-content: center; gap: 34px; }
  .card-back .brand-name { font-size: 32px; }
  .card-back .brand-mark { width: 46px; height: 46px; }
  .website { font-size: 17px; font-weight: 400; color: var(--ink); letter-spacing: 0.5px; }
</style>
</head>
<body>
<main class="sheet">
  <section class="card card-front" aria-label="Business card front">
    <div class="brand">
      <span class="brand-mark"></span>
      <span class="brand-name">Brightwick Gadget Clinic</span>
    </div>
    <div class="band-rule top"></div>
    <div class="name-band">
      <span class="person-name">Marcus Delgrove</span>
      <span class="band-divider"></span>
      <span class="person-role">Store Manager</span>
    </div>
    <div class="band-rule bottom"></div>
    <div class="contact-row">
      <div class="phone">
        <span>(210) 555-0147</span>
        <span class="phone-icon">
          <svg width="10" height="10" viewBox="0 0 24 24" aria-hidden="true"><path fill="#fff" d="M6.6 10.8a15.1 15.1 0 0 0 6.6 6.6l2.2-2.2a1 1 0 0 1 1-.25 11.4 11.4 0 0 0 3.6.57 1 1 0 0 1 1 1V20a1 1 0 0 1-1 1A17 17 0 0 1 3 4a1 1 0 0 1 1-1h3.5a1 1 0 0 1 1 1c0 1.25.2 2.45.57 3.57a1 1 0 0 1-.25 1z"/></svg>
        </span>
      </div>
      <span class="contact-divider"></span>
      <address class="address" style="font-style:normal">
        4810 E Harlow Ridge Rd<br>
        Suite 417<br>
        San Antonio, TX 78163
      </address>
    </div>
  </section>

  <section class="card card-back" aria-label="Business card back">
    <div class="brand">
      <span class="brand-mark"></span>
      <span class="brand-name">Brightwick Gadget Clinic</span>
    </div>
    <span class="website">www.BrightwickClinic.com</span>
  </section>
</main>
</body>
</html>
```